Website design for legal tech start up in Switzerland (B2B)

We are for a legal tech start up in Switzerland called KOVA. We have been running since August 2016. This will be our first live website.

We need a website designed and business card design for our start-up in Switzerland. We also need the Web design to be converted into HTML and CSS files.

Function of website:
• To inform potential customers of our services
• Form a key part of our digital marketing and sales footprint.
• Branding

Please find attached logo.
Updates

Project Deadline Extended Reason: Giving us time to review submissions and provide opportunity for more submissions. Added Thursday, February 16, 2017

Project Deadline Extended
Reason: Looking for more idea's not necessarily set on blue and grey colours only.

Target Market(s)

B2B tech powered legal services.

Industry/Entity Type

Legal

Contact Information for Business Card

Lean and slick design.

Coding

Coded - Design and coding required

Number of Pages Required

5+ page

Requirements
Must have
• VERY LEAN AND CLEAN DESIGN!
• We have received many great standard designs, but we are looking for something more out-of-the box: You can get inspiration from these designs: http://www.pixelvane.com/websites/clean/
• Thanks!!
• Easy content management system
• Well structured coding for additional development
• Responsive webpage for all types of devices
• SEO optimized
• Tabs (Home, services, team, careers, blog, contact us)
• Colour scheme complementary to logo
Nice to have
• Look and Design - Approachable, High-tech, Modern
• Easy to add chat bot capability in future
Should not have
• Too busy/ too much clutter
• Not take to long to load

```html
<!DOCTYPE html>
<html lang="en">
<head>
<meta charset="utf-8">
<title>KOVA — Legal Tech</title>
<link href="https://fonts.googleapis.com/css2?family=Roboto:wght@300;400&family=Open+Sans:wght@400;600&display=swap" rel="stylesheet">
<style>
:root{
  --navy:#1d3a6b;
  --ink:#2b2b2b;
  --heading:#333;
  --muted:#8a8a8a;
  --rule:#e3e3e3;
  --footer-bg:#f4f4f4;
  --white:#fff;
}
*{margin:0;padding:0;box-sizing:border-box}
html,body{width:686px;height:1200px;overflow:hidden;background:var(--white)}
body{position:relative;font-family:"Open Sans",Arial,sans-serif;color:var(--ink)}
.abs{position:absolute}
.site-header{position:absolute;left:0;top:0;width:686px;height:58px;border-top:2px solid var(--navy);background:var(--white)}
.brand{position:absolute;left:76px;top:12px;font-family:"Roboto",sans-serif;font-weight:400;font-size:31px;letter-spacing:2px;color:var(--heading);line-height:1}
.search-icon{position:absolute;left:599px;top:15px}
.main-nav{position:absolute;top:40px;left:0;width:686px;font-family:"Roboto",sans-serif;font-size:7px;letter-spacing:.6px;color:#666}
.main-nav a{position:absolute;text-decoration:none;color:inherit}
.main-nav a.active{color:var(--navy);}
.main-nav a.active::after{content:"";position:absolute;left:-2px;right:-2px;top:13px;height:2px;background:var(--navy)}
.hero{position:absolute;left:0;top:58px;width:686px;height:262px;background:linear-gradient(180deg,#7a6e62 0%,#8a6f58 35%,#6e5f50 60%,#2f4a45 85%,#3a4a42 100%)}
.hero::before{content:"";position:absolute;inset:0;background:rgba(20,25,30,.3)}
.hero-title{position:absolute;top:66px;width:686px;text-align:center;font-family:"Roboto",sans-serif;font-weight:300;font-size:29px;color:var(--white);letter-spacing:.5px}
.hero-sub{position:absolute;top:112px;width:686px;text-align:center;font-size:11px;font-weight:600;color:var(--white);letter-spacing:.2px}
.btn{display:inline-block;background:var(--navy);color:var(--white);font-size:8.5px;text-align:center;letter-spacing:.3px}
.hero .btn{position:absolute;left:305px;top:153px;width:76px;height:23px;line-height:23px}
.dots{position:absolute;top:231px;left:327px;display:flex;gap:5px}
.dots span{width:7px;height:7px;border-radius:50%;background:#aaa}
.dots span:first-child{background:var(--white)}
.section-title{font-family:"Roboto",sans-serif;font-weight:300;color:var(--heading);font-size:19px;letter-spacing:.3px}
.body-text{font-size:6.3px;line-height:13.6px;color:var(--muted)}
.welcome-title{left:76px;top:358px}
.welcome-text{left:76px;top:390px;width:260px;text-align:justify}
.welcome .btn{position:absolute;left:76px;top:489px;width:77px;height:24px;line-height:24px}
.video{left:375px;top:362px;width:237px;height:140px;border:1px solid #ddd;padding:3px;background:var(--white)}
.video-media{width:100%;height:100%;background:linear-gradient(135deg,#b9cbd6 0%,#e8ecef 45%,#c7a590 75%,#a0776a 100%);position:relative}
.video-media svg{position:absolute;left:97px;top:50px}
.divider{left:76px;width:535px;height:1px;background:var(--rule)}
.center{width:686px;text-align:center}
.services-intro{top:612px;font-size:6px;color:var(--muted)}
.service{width:160px;text-align:center}
.service-title{font-family:"Roboto",sans-serif;font-weight:300;font-size:11.5px;color:var(--heading);margin-top:14px}
.service p{font-size:6.3px;line-height:11px;color:var(--muted);margin-top:8px;padding:0 6px}
.service .more{display:block;margin-top:12px;font-size:6px;color:var(--ink)}
.service svg{display:block;margin:0 auto}
.post{width:270px;height:78px}
.post-media{position:absolute;left:0;top:0;width:90px;height:78px}
.post-date{position:absolute;left:102px;top:0;font-size:5.8px;color:#666}
.post-title{position:absolute;left:102px;top:15px;font-family:"Roboto",sans-serif;font-weight:300;font-size:11.5px;line-height:16.5px;color:var(--heading)}
.post-text{position:absolute;left:102px;top:54px;width:149px;font-size:5.8px;line-height:10.5px;color:var(--muted);text-align:justify}
.site-footer{position:absolute;left:0;top:1022px;width:686px;height:178px;background:var(--footer-bg)}
.footer-brand{position:absolute;left:76px;top:21px;font-family:"Roboto",sans-serif;font-size:36px;letter-spacing:2px;color:var(--heading);line-height:1}
.social{position:absolute;left:76px;top:68px;display:flex;gap:3px}
.social span{width:18px;height:18px;border:1px solid #333;border-radius:50%}
.footer-head{position:absolute;top:23px;font-size:6.3px;color:#444;letter-spacing:.2px}
.quick-links{position:absolute;left:231px;top:44px;list-style:none;font-size:6.3px;color:#444;line-height:13.7px}
.news-text{position:absolute;left:324px;top:44px;width:160px;font-size:5.8px;line-height:13.7px;color:#444}
.news-input{position:absolute;left:322px;top:76px;width:144px;height:24px;background:var(--white);border:1px solid #ddd;font-size:5.8px;color:#555;padding:0 9px;line-height:22px}
.site-footer .btn{position:absolute;left:324px;top:111px;width:47px;height:15px;line-height:15px;font-size:6px}
.contact-list{position:absolute;left:517px;top:44px;list-style:none;font-size:6px;color:#444}
.contact-list li{display:flex;gap:7px;align-items:flex-start;height:15.5px}
.contact-list svg{flex:none;margin-top:1px}
.contact-list u{color:#444}
.footer-rule{position:absolute;left:76px;top:146px;width:535px;height:1px;background:#ddd}
.copyright{position:absolute;top:157px;width:686px;text-align:center;font-size:5.8px;color:#777}
</style>
</head>
<body>

<header class="site-header">
  <div class="brand">KOVA</div>
  <svg class="search-icon" width="12" height="12" viewBox="0 0 12 12"><circle cx="5" cy="5" r="4" fill="none" stroke="#555" stroke-width="1"/><line x1="8" y1="8" x2="11.5" y2="11.5" stroke="#555" stroke-width="1"/></svg>
  <nav class="main-nav">
    <a class="active" style="left:333px">HOME</a>
    <a style="left:377px">SERVICES</a>
    <a style="left:435px">TEAM</a>
    <a style="left:477px">CAREERS</a>
    <a style="left:529px">BLOG</a>
    <a style="left:570px">CONTACT US</a>
  </nav>
</header>

<section class="hero" role="img" aria-label="Aerial view of a Swiss old town by the river">
  <h1 class="hero-title">LEGAL ADVICE</h1>
  <p class="hero-sub">LOREM IPSUM DOLOR SIT AMET, CONSECTETUR ADIPISCING ELIT</p>
  <span class="btn">FIND OUT HOW</span>
  <div class="dots"><span></span><span></span><span></span></div>
</section>

<section class="welcome">
  <h2 class="section-title abs welcome-title">WELCOME TO KOVA</h2>
  <p class="body-text abs welcome-text">Nemo enim ipsam voluptatem quia voluptas sit aspernatur aut odit aut fugit, sed quia consequuntur magni dolores eos qui ratione voluptatem sequi nesciunt. Neque porro quisquam est, qui dolorem ipsum quia dolor sit amet, consectetur, adipisci velit, sed quia non numquam eius modi tempora incidunt ut labore et dolore magnam aliquam quaerat voluptatem. Ut enim ad minima veniam, quis nostrum exercitationem ullam corporis suscipit laboriosam, nisi ut aliquid ex ea commodi</p>
  <span class="btn">READ MORE</span>
  <div class="abs video">
    <div class="video-media" role="img" aria-label="Video still of a hand signing a contract at a desk">
      <svg width="36" height="36" viewBox="0 0 36 36"><circle cx="18" cy="18" r="16" fill="rgba(255,255,255,.25)" stroke="#444" stroke-width="2"/><path d="M14 10 L26 18 L14 26 Z" fill="#444"/></svg>
    </div>
  </div>
</section>

<div class="abs divider" style="top:546px"></div>

<section class="services">
  <h2 class="section-title abs center" style="top:571px">OUR SERVICES</h2>
  <p class="abs center services-intro">Nemo enim ipsam voluptatem quia voluptas sit aspernatur aut odit aut fugit, sed quia consequuntur magni dolores eos qui ratione voluptatem sequi nesciunt.</p>

  <div class="abs service" style="left:68px;top:645px">
    <svg width="22" height="24" viewBox="0 0 22 24"><rect x="1" y="1" width="20" height="22" rx="2" fill="none" stroke="#1d3a6b" stroke-width="2"/><rect x="4" y="4" width="14" height="4" fill="#1d3a6b"/><g fill="#1d3a6b"><rect x="4" y="10" width="3" height="3"/><rect x="9.5" y="10" width="3" height="3"/><rect x="15" y="10" width="3" height="3"/><rect x="4" y="14.5" width="3" height="3"/><rect x="9.5" y="14.5" width="3" height="3"/><rect x="15" y="14.5" width="3" height="3"/><rect x="4" y="19" width="3" height="2"/><rect x="9.5" y="19" width="3" height="2"/><rect x="15" y="19" width="3" height="2"/></g></svg>
    <h3 class="service-title">LEGAL ADVICE</h3>
    <p>Nemo enim ipsam voluptatem quia voluptas sit aspernatur aut odit aut fugit, sed quia consequuntur magni dolores eos</p>
    <span class="more">READ MORE &gt;</span>
  </div>

  <div class="abs service" style="left:263px;top:645px">
    <svg width="26" height="24" viewBox="0 0 26 24"><path d="M1 5 L1 21 L11 21 Q13 22 15 21 L25 21 L25 5 L23 5 L23 19 L15 19 Q13 20 11 19 L3 19 L3 5 Z" fill="#1d3a6b"/><path d="M4 4 Q9 2 12.5 5 L12.5 18 Q9 15.5 4 17 Z M21.5 4 Q17 2 13.5 5 L13.5 18 Q17 15.5 21.5 17 Z" fill="none" stroke="#1d3a6b" stroke-width="1.6"/></svg>
    <h3 class="service-title">MIGRATION CONSULTANCY</h3>
    <p>Nemo enim ipsam voluptatem quia voluptas sit aspernatur aut odit aut fugit, sed quia consequuntur magni dolores eos</p>
    <span class="more">READ MORE &gt;</span>
  </div>

  <div class="abs service" style="left:458px;top:645px">
    <svg width="24" height="22" viewBox="0 0 24 22"><rect x="8" y="1" width="8" height="5" rx="1" fill="none" stroke="#1d3a6b" stroke-width="2"/><rect x="1" y="5" width="22" height="16" rx="2" fill="#1d3a6b"/><rect x="1" y="11" width="22" height="1.5" fill="#fff"/><rect x="10" y="9.5" width="4" height="4" fill="#fff"/></svg>
    <h3 class="service-title">BUSINESS CONSULTANCY</h3>
    <p>Nemo enim ipsam voluptatem quia voluptas sit aspernatur aut odit aut fugit, sed quia consequuntur magni dolores eos</p>
    <span class="more">READ MORE &gt;</span>
  </div>
</section>

<div class="abs divider" style="top:834px"></div>

<section class="blog">
  <h2 class="section-title abs center" style="top:859px">RECENT BLOG</h2>
  <article class="abs post" style="left:76px;top:910px">
    <div class="post-media" role="img" aria-label="Top-down photo of a team meeting around a table" style="background:linear-gradient(135deg,#e4e7ea,#9aa3ab 55%,#5d6670)"></div>
    <span class="post-date">Feb 08,2017</span>
    <h3 class="post-title">LEGAL ADVICES FOR<br>COMPANY</h3>
    <p class="post-text">Nemo enim ipsam voluptatem quia voluptas sit aspernatur aut odit aut fugit</p>
  </article>
  <article class="abs post" style="left:361px;top:910px">
    <div class="post-media" role="img" aria-label="Photo of colleagues reviewing documents together" style="background:linear-gradient(135deg,#d8d2c8,#b7b1a8 45%,#4b4f58)"></div>
    <span class="post-date">Feb 08,2017</span>
    <h3 class="post-title">LEGAL ADVICES FOR<br>COMPANY</h3>
    <p class="post-text">Nemo enim ipsam voluptatem quia voluptas sit aspernatur aut odit aut fugit</p>
  </article>
</section>

<footer class="site-footer">
  <div class="footer-brand">KOVA</div>
  <div class="social" aria-label="Social links"><span></span><span></span><span></span><span></span></div>

  <h4 class="footer-head" style="left:230px">QUICK LINKS</h4>
  <ul class="quick-links">
    <li>Home</li><li>Services</li><li>Team</li><li>Careers</li><li>Blog</li><li>Contact us</li>
  </ul>

  <h4 class="footer-head" style="left:322px">NEWSLETTER</h4>
  <p class="news-text">Enter your email address to receive the latest news and notes from our blog.</p>
  <div class="news-input">Enter Your Mail Id</div>
  <span class="btn">SUBSCRIBE</span>

  <h4 class="footer-head" style="left:517px">CONTACT US</h4>
  <ul class="contact-list">
    <li><svg width="8" height="7" viewBox="0 0 8 7"><path d="M0 2 Q4 -1 8 2 L7 3 L5.5 2 L2.5 2 L1 3 Z M1.5 3.5 L6.5 3.5 L7 7 L1 7 Z" fill="#555"/></svg>(044) 512-7730</li>
    <li><svg width="8" height="7" viewBox="0 0 8 7"><rect x="2" y="0" width="4" height="2" fill="#555"/><rect x="0" y="2" width="8" height="3.5" fill="#555"/><rect x="2" y="4.5" width="4" height="2.5" fill="#555"/></svg>(044) 512-7730</li>
    <li><svg width="8" height="6" viewBox="0 0 8 6"><rect x="0" y="0" width="8" height="6" fill="#555"/><path d="M0 0 L4 3.5 L8 0" fill="none" stroke="#f4f4f4" stroke-width=".8"/></svg><u>info@kova-mail.ch</u></li>
    <li style="line-height:8px"><svg width="6" height="8" viewBox="0 0 6 8"><path d="M3 8 L0.5 4 A3 3 0 1 1 5.5 4 Z" fill="#555"/><circle cx="3" cy="3" r="1" fill="#f4f4f4"/></svg><span>#1204 Lorem ipsum dolor sit<br>amet, consectetur</span></li>
  </ul>

  <div class="footer-rule"></div>
  <p class="copyright">©2017 Kova.All Rights Reserved.</p>
</footer>

</body>
</html>
```